Business Card Design needed - Something Awesome!

Need a business card designed. Company is "Marlowe Advisory" we do consulting and also have sales automation technology.
I'm going to use thick stock or metal, something really nice... I was thinking about a QR Code on the back that would just upload my contact info to the persons contact, etc -

This is a Strategy Company with a tech feel. I'm open to ideas but really want this to be nice!

I need a template that should include:

Name | Position or Title
D: 415.902.3376
www.marloweadvisory.example

I'm going to attach my contact so you can use that one, I need to get this printed.

Target Market(s)

Small to mid size customers, Entrepreneurs etc.

Industry/Entity Type

Consulting, Tech, Private Equity.

Contact Information for Business Card

Name, Phone, Maybe email, URL

Font styles to use
Sans Serif

Colors

Designer to choose only greyscale colors for use in the design.

Requirements
Must have
• Fresh, Clean, stand out from the crowd - will be on thick stock or metal.
Nice to have
• Clean, simple yet impactful.
Should not have
• Not cartoonish

```html
<!DOCTYPE html>
<html lang="en">
<head>
<meta charset="utf-8">
<title>Marlowe Advisory – Business Card</title>
<link href="https://fonts.googleapis.com/css2?family=Arimo:wght@400;700&display=swap" rel="stylesheet">
<style>
  :root {
    --backdrop: #3a3a3a;
    --card: #0d0d0d;
    --silver: #cfcfcf;
    --silver-dim: #9a9a9a;
    --rule: #5a5a5a;
  }
  * { margin: 0; padding: 0; box-sizing: border-box; }
  html, body {
    width: 1200px; height: 801px; overflow: hidden;
    background: var(--backdrop);
    font-family: "Arimo", Arial, sans-serif;
  }
  .sheet {
    width: 1200px; height: 801px;
    display: flex; align-items: center; justify-content: center; gap: 48px;
  }
  .card {
    width: 525px; height: 300px;
    background: var(--card);
    position: relative;
  }
  .card-front {
    display: flex; align-items: center;
    padding: 0 36px 0 44px;
  }
  .brand {
    display: flex; align-items: center; gap: 10px;
    width: 210px;
  }
  .brand-name {
    font-size: 34px; font-weight: 400; letter-spacing: 2px;
    color: var(--silver);
  }
  .brand-square {
    width: 12px; height: 12px; background: var(--silver);
  }
  .divider {
    width: 1px; height: 110px; background: var(--rule);
    margin-right: 24px;
  }
  .details { color: var(--silver); }
  .person-name {
    font-size: 16px; font-weight: 700; letter-spacing: 0.5px;
    text-transform: uppercase;
  }
  .person-title {
    font-size: 13px; color: var(--silver-dim); margin: 4px 0 16px;
  }
  .contact-list { list-style: none; }
  .contact-item {
    display: flex; align-items: center; gap: 7px;
    font-size: 12.5px; line-height: 19px;
  }
  .contact-icon { width: 10px; height: 10px; fill: var(--silver); flex: none; }
  .card-back {
    display: flex; align-items: center; justify-content: center; gap: 14px;
  }
  .card-back .brand-square { width: 20px; height: 20px; }
  .card-back .brand-name { font-size: 30px; }
</style>
</head>
<body>
<main class="sheet">
  <section class="card card-front" aria-label="Card front">
    <div class="brand">
      <span class="brand-name">MARLOWE</span>
      <span class="brand-square"></span>
    </div>
    <div class="divider"></div>
    <div class="details">
      <p class="person-name">Elias R. Thornbury</p>
      <p class="person-title">Founder / CEO</p>
      <ul class="contact-list">
        <li class="contact-item">
          <svg class="contact-icon" viewBox="0 0 10 10"><path d="M2 0.5 L3.6 0.5 L4.2 2.8 L3 3.8 Q4 6 6.2 7 L7.2 5.8 L9.5 6.4 L9.5 8 Q9.5 9.5 8 9.5 Q0.5 9 0.5 2 Q0.5 0.5 2 0.5Z"/></svg>
          415.902.3376
        </li>
        <li class="contact-item">
          <svg class="contact-icon" viewBox="0 0 10 10"><path d="M0.5 2 H9.5 V8.5 H0.5Z M0.5 2 L5 5.5 L9.5 2" fill="none" stroke="#cfcfcf" stroke-width="1"/></svg>
          info@marloweadvisory.example
        </li>
        <li class="contact-item">
          <svg class="contact-icon" viewBox="0 0 10 10"><circle cx="5" cy="5" r="4.3" fill="none" stroke="#cfcfcf" stroke-width="1"/><path d="M0.7 5 H9.3 M5 0.7 Q2.5 5 5 9.3 M5 0.7 Q7.5 5 5 9.3" fill="none" stroke="#cfcfcf" stroke-width="0.8"/></svg>
          www.marloweadvisory.example
        </li>
      </ul>
    </div>
  </section>
  <section class="card card-back" aria-label="Card back">
    <span class="brand-name">MARLOWE</span>
    <span class="brand-square"></span>
  </section>
</main>
</body>
</html>
```